Employee Benefits Flyer for Recruiting

We are a Steel Product Supplier and Manufacturer in Toledo Ohio.

We would like to create an "attention getting", one-page handout to give prospective employees (both production and administrative) that illustrates all the benefits we offer as a company. An editable document would be preferable as we add more or change existing benefits in the future. Current benefits include:

Individual and Family Medical Insurance
Dental Insurance
Vision Insurance
Short Term Disability Insurance
Critical Illness and Accident Insurance
No Cost Life Insurance Policy
Education Cost Reimbursement
401K with Company Match
Profit Sharing
Attendance and Performance Bonuses
No Cost Legal Assistance
No Cost Counseling Services
No Cost Tobacco Cessation Coaching
No Cost College Planning Assistance
No Cost Work-Life Services
No Cost Employee Discounts
No Cost Legal Consultation
No Cost Financial Consultation
No Cost ID Theft Assistance
No Cost Tax Consultation Assistance
Up to 17 Days of Paid Time Off

Target Market(s)

Potential Employees

Industry/Entity Type

Industrial Manufacturing

Requirements
Must have
• Nicely laid out illustrations / engaging content

```html
<!DOCTYPE html>
<html lang="en">
<head>
<meta charset="utf-8">
<title>Employee Benefits – Ironvale Metal Works</title>
<link rel="stylesheet" href="https://fonts.googleapis.com/css2?family=Montserrat:wght@500;600;800&display=swap">
<style>
  :root {
    --page-bg: #525252;
    --paper: #ffffff;
    --brand-blue: #0a48b4;
    --brand-dark: #2b3441;
    --panel-edge: #1b232d;
    --panel-mid: #3f5670;
    --band-deep: #0b2c72;
    --band-bright: #0b62d8;
    --photo-blue: #3d7cc2;
    --photo-grey: #8d9aa6;
    --list-text: #ffffff;
  }
  * { margin: 0; padding: 0; box-sizing: border-box; }
  html, body { width: 1200px; height: 927px; overflow: hidden; }
  body {
    background: var(--page-bg);
    font-family: "Montserrat", Arial, sans-serif;
    position: relative;
  }
  .flyer {
    position: absolute;
    left: 120px; top: 93px;
    width: 960px; height: 741px;
    background: var(--paper);
    overflow: hidden;
  }
  .hero {
    position: absolute; left: 0; top: 0;
    width: 960px; height: 364px;
    background: var(--paper);
  }
  .hero-photo {
    position: absolute; left: 0; top: 0;
    width: 540px; height: 364px;
    background:
      linear-gradient(to right, rgba(255,255,255,0) 0%, rgba(255,255,255,0) 62%, #ffffff 100%),
      linear-gradient(160deg, var(--photo-grey) 0%, var(--photo-blue) 38%, #4b6d8e 62%, #4f6b3a 100%);
  }
  .brand {
    position: absolute;
    left: 612px; top: 120px;
    width: 240px;
    display: flex; align-items: center; justify-content: center; gap: 8px;
    font-weight: 800; font-size: 19px; letter-spacing: 0.5px;
    color: var(--brand-blue);
    white-space: nowrap;
  }
  .brand-dot {
    width: 14px; height: 14px; border-radius: 50%;
    background: var(--brand-blue);
  }
  .headline {
    position: absolute;
    left: 542px; top: 214px;
    font-weight: 500;
    font-size: 70px;
    line-height: 64px;
    letter-spacing: 1px;
    color: var(--brand-blue);
  }
  .benefits {
    position: absolute; left: 0; top: 364px;
    width: 960px; height: 357px;
    background: linear-gradient(to right, var(--panel-edge) 0%, var(--panel-mid) 50%, var(--panel-edge) 100%);
  }
  .benefit-list {
    position: absolute; top: 14px;
    list-style: none;
  }
  .benefit-list.left { left: 37px; }
  .benefit-list.right { left: 527px; }
  .benefit-list li {
    display: flex; align-items: center; gap: 11px;
    height: 30.5px;
    font-weight: 500; font-size: 17.5px;
    color: var(--list-text);
    letter-spacing: 0.3px;
    white-space: nowrap;
  }
  .tick { width: 13px; height: 13px; flex: none; }
  .accent-band {
    position: absolute; left: 0; bottom: 0;
    width: 960px; height: 20px;
    background: linear-gradient(to right, var(--band-deep) 0%, var(--band-bright) 50%, var(--band-deep) 100%);
  }
</style>
</head>
<body>
<svg width="0" height="0" style="position:absolute">
  <defs>
    <symbol id="tick" viewBox="0 0 16 16">
      <circle cx="8" cy="8" r="8" fill="#ffffff"/>
      <path d="M4.3 8.3 L7 10.8 L11.8 5.6" fill="none" stroke="#1f2a36" stroke-width="2.2" stroke-linecap="round" stroke-linejoin="round"/>
    </symbol>
  </defs>
</svg>

<main class="flyer">
  <header class="hero">
    <div class="hero-photo" role="img" aria-label="Aerial photo of the company's blue steel-clad manufacturing building with lawn in front"></div>
    <div class="brand"><span class="brand-dot"></span>IRONVALE METAL WORKS</div>
    <h1 class="headline">EMPLOYEE<br>BENEFITS</h1>
  </header>

  <section class="benefits">
    <ul class="benefit-list left">
      <li><svg class="tick"><use href="#tick"/></svg>Individual and Family Medical Insurance</li>
      <li><svg class="tick"><use href="#tick"/></svg>Dental Insurance</li>
      <li><svg class="tick"><use href="#tick"/></svg>Vision Insurance</li>
      <li><svg class="tick"><use href="#tick"/></svg>Short Term Disability Insurance</li>
      <li><svg class="tick"><use href="#tick"/></svg>Critical Illness and Accident Insurance</li>
      <li><svg class="tick"><use href="#tick"/></svg>No Cost Life Insurance Policy</li>
      <li><svg class="tick"><use href="#tick"/></svg>Education Cost Reimbursement</li>
      <li><svg class="tick"><use href="#tick"/></svg>401K with Company Match</li>
      <li><svg class="tick"><use href="#tick"/></svg>Profit Sharing</li>
      <li><svg class="tick"><use href="#tick"/></svg>Attendance and Performance Bonuses</li>
      <li><svg class="tick"><use href="#tick"/></svg>No Cost Legal Assistance</li>
    </ul>
    <ul class="benefit-list right">
      <li><svg class="tick"><use href="#tick"/></svg>No Cost Counseling Services</li>
      <li><svg class="tick"><use href="#tick"/></svg>No Cost Tobacco Cessation Coaching</li>
      <li><svg class="tick"><use href="#tick"/></svg>No Cost College Planning Assistance</li>
      <li><svg class="tick"><use href="#tick"/></svg>No Cost Work-Life Services</li>
      <li><svg class="tick"><use href="#tick"/></svg>No Cost Employee Discounts</li>
      <li><svg class="tick"><use href="#tick"/></svg>No Cost Legal Consultation</li>
      <li><svg class="tick"><use href="#tick"/></svg>No Cost Financial Consultation</li>
      <li><svg class="tick"><use href="#tick"/></svg>No Cost ID Theft Assistance</li>
      <li><svg class="tick"><use href="#tick"/></svg>No Cost Tax Consultation Assistance</li>
      <li><svg class="tick"><use href="#tick"/></svg>Up to 17 Days of Paid Time Off</li>
    </ul>
  </section>

  <div class="accent-band"></div>
</main>
</body>
</html>
```